Bry7Legal Letterhead

Need a new letterhead for my law firm.
IDENTIFYING INFORMATION BELOW:
Anselmo R Quintara III
Attorney at Law
Address: 2847 Larkspur Blvd, Ste 300, Dallas, TX 75204
Phone: 877-482-6017
Fax: 469-738-1452
Email: bry@bry7legal.example
Website: www.bry7legal.example

Colors
0054AA
0677BA
7BADD7
CADEEF
E8F1F8

Requirements
Must have
• Logo needs to be on the letterhead, along with identifying information which is included in the project description.

```html
<!DOCTYPE html>
<html lang="en">
<head>
<meta charset="utf-8">
<title>Bry7Legal Letterhead</title>
<link rel="stylesheet" href="https://fonts.googleapis.com/css2?family=Arimo:ital,wght@0,400;0,700;1,400&family=Great+Vibes&display=swap">
<style>
  :root {
    --ink: #111111;
    --blue-deep: #1a4ff0;
    --blue-mid: #2f7fe6;
    --blue-soft: #7bc8ef;
    --blue-pale: #cadeef;
    --panel: #f2f9fd;
    --paper: #ffffff;
  }
  * { margin: 0; padding: 0; box-sizing: border-box; }
  html, body { width: 848px; height: 1200px; overflow: hidden; background: var(--paper); }
  body { font-family: "Arimo", Arial, sans-serif; color: var(--ink); }
  .letterhead { position: relative; width: 848px; height: 1200px; background: var(--paper); }

  .brand-name {
    position: absolute; left: 51px; top: 50px;
    font-family: "Arimo", Arial, sans-serif; font-weight: 700;
    font-size: 38px; line-height: 1; color: var(--ink); letter-spacing: 1px;
  }
  .header-rule {
    position: absolute; left: 0; top: 121px; width: 490px; height: 7px;
    background: linear-gradient(90deg, var(--blue-deep) 0%, #8fb0f5 60%, rgba(202,222,239,0) 100%);
  }
  .wave-art {
    position: absolute; left: 478px; top: 68px; width: 370px; height: 70px;
    border-radius: 35px 0 0 35px;
    background: linear-gradient(90deg, rgba(200,235,248,0.6) 0%, var(--blue-soft) 35%, var(--blue-mid) 65%, var(--blue-deep) 100%);
  }

  .letter-panel {
    position: absolute; left: 84px; top: 179px; width: 680px; height: 858px;
    background: var(--panel);
  }
  .salutation { position: absolute; left: 51px; top: 33px; font-size: 16px; }
  .signature-script {
    position: absolute; left: 49px; top: 704px;
    font-family: "Great Vibes", cursive; font-size: 32px; line-height: 1;
  }
  .signature-line {
    position: absolute; left: 49px; top: 746px; width: 185px; height: 1.5px; background: var(--ink);
  }
  .signer-name { position: absolute; left: 51px; top: 758px; font-weight: 700; font-size: 17px; }
  .signer-title { position: absolute; left: 51px; top: 779px; font-style: italic; font-size: 16px; }

  .footer-rule {
    position: absolute; left: 0; top: 1081px; width: 848px; height: 7px;
    background: linear-gradient(90deg, var(--blue-deep) 0%, #8fb0f5 55%, #e8f1f8 100%);
  }
  .contact-bar {
    position: absolute; left: 88px; right: 56px; top: 1102px; height: 30px;
    display: flex; justify-content: space-between; align-items: center;
  }
  .contact-item {
    display: flex; align-items: center; white-space: nowrap;
    font-size: 10.5px; line-height: 1.3; color: var(--ink);
  }
  .contact-item svg { width: 15px; height: 15px; flex: none; margin-right: 10px; }
</style>
</head>
<body>
<div class="letterhead">
  <div class="brand-name">Bry7Legal</div>
  <div class="header-rule"></div>
  <div class="wave-art" role="img" aria-label="Decorative blue ocean wave flourish"></div>

  <main class="letter-panel">
    <p class="salutation">To</p>
    <p class="signature-script">Digital Signature</p>
    <div class="signature-line"></div>
    <p class="signer-name">Anselmo R Quintara III</p>
    <p class="signer-title">Attorney at Law</p>
  </main>

  <div class="footer-rule"></div>

  <footer class="contact-bar">
    <div class="contact-item contact-phone">
      <svg viewBox="0 0 24 24"><path d="M6 2l3 1 1 5-2 2c1 3 3 5 6 7l2-2 5 1 1 3-2 3C10 22 2 14 3 4z" fill="var(--ink)"/></svg>
      <span>877-482-6017</span>
    </div>
    <div class="contact-item contact-fax">
      <svg viewBox="0 0 24 24"><rect x="6" y="2" width="12" height="8" fill="none" stroke="var(--ink)" stroke-width="2"/><rect x="2" y="10" width="20" height="12" rx="2" fill="var(--ink)"/><circle cx="12" cy="16" r="3" fill="var(--paper)"/></svg>
      <span>469-738-1452</span>
    </div>
    <div class="contact-item contact-email">
      <svg viewBox="0 0 24 24"><rect x="1" y="5" width="22" height="14" fill="var(--ink)"/><path d="M1 5l11 8 11-8" fill="none" stroke="var(--paper)" stroke-width="1.5"/></svg>
      <span>bry@bry7legal.example</span>
    </div>
    <div class="contact-item contact-web">
      <svg viewBox="0 0 24 24" fill="none" stroke="var(--ink)" stroke-width="1.5"><circle cx="12" cy="12" r="10"/><ellipse cx="12" cy="12" rx="4.5" ry="10"/><path d="M2 12h20M4 7h16M4 17h16"/></svg>
      <span>www.bry7legal.example</span>
    </div>
    <div class="contact-item contact-address">
      <svg viewBox="0 0 24 24"><path d="M12 1a7 7 0 0 0-7 7c0 5 7 12 7 12s7-7 7-12a7 7 0 0 0-7-7z" fill="var(--ink)"/><circle cx="12" cy="8" r="2.5" fill="var(--paper)"/><ellipse cx="12" cy="21" rx="8" ry="2" fill="none" stroke="var(--ink)" stroke-width="1.2"/></svg>
      <span>2847 Larkspur Blvd, Ste<br>300, Dallas, TX 75204</span>
    </div>
  </footer>
</div>
</body>
</html>
```